Business Card and Letterhead for Pimlu - modern real estate business

I need a double sided business card design for Pimlu. Please see business card brief here https://files.trelvonadocs.com/sheet/r/7QzTmWbaXLJnoPEd-kRyUgFhHsstbvCe2qfoMxDa_pz/view?mode=shared

Please feel free to design the business cards however you feel best. I am happy to give some creative freedoms and then provide feedback from there.

Please then also create a letterhead to match the business card design

Colors

Designer to choose colors to be used in the design.

Requirements
Must have
• Must be a modern, elegant business card which looks very professional

```html
<!DOCTYPE html>
<html lang="en">
<head>
<meta charset="utf-8">
<title>Pimlu Business Card</title>
<link rel="stylesheet" href="https://fonts.googleapis.com/css2?family=Michroma&family=Titillium+Web:wght@300&display=swap">
<style>
  :root {
    --stage: #1b1b1b;
    --card: #060606;
    --red: #e8202a;
    --red-deep: #a81c22;
    --grey: #5a5a5a;
    --white: #ffffff;
    --text: #f2f2f2;
    --display: "Michroma", sans-serif;
    --body: "Titillium Web", sans-serif;
  }
  * { margin: 0; padding: 0; box-sizing: border-box; }
  html, body {
    width: 907px; height: 1200px; overflow: hidden;
    background: var(--stage);
  }
  .canvas { position: relative; width: 907px; height: 1200px; }
  .card {
    position: absolute; width: 547px; height: 338px;
    background: var(--card); overflow: hidden;
  }
  .card-front { left: 174px; top: 192px; }
  .card-back { left: 195px; top: 631px; }
  .card-art { position: absolute; inset: 0; width: 100%; height: 100%; }

  .wordmark {
    position: absolute; font-family: var(--display);
    color: var(--red); font-weight: 400; text-align: center;
    letter-spacing: 2px; line-height: 1; white-space: nowrap;
  }
  .card-front .wordmark { left: 174px; top: 80px; width: 324px; font-size: 56px; }
  .card-back .wordmark { left: 86px; top: 136px; width: 375px; font-size: 64px; }

  .agent-photo {
    position: absolute; left: 21px; top: 172px; width: 120px; height: 120px;
    border-radius: 18px;
    background: linear-gradient(160deg, #c9d3d6 0%, #8d9a84 45%, #3a3d3f 75%, #1d1e20 100%);
  }
  .agent-name {
    position: absolute; left: 161px; top: 190px;
    font-family: var(--display); font-size: 15px; color: var(--white);
    letter-spacing: 0.5px; line-height: 1;
  }
  .agent-role {
    position: absolute; left: 161px; top: 207px;
    font-family: var(--body); font-weight: 300; font-size: 13px; color: var(--text);
  }
  .contact {
    position: absolute; top: 238px;
    font-family: var(--body); font-weight: 300; font-size: 13px;
    line-height: 16px; color: var(--text); list-style: none;
  }
  .contact-direct { left: 161px; }
  .contact-office { right: 46px; text-align: right; }

  .web-address {
    position: absolute; left: 209px; top: 228px; width: 125px;
    text-align: center; font-family: var(--body); font-weight: 300;
    font-size: 16px; color: var(--text); line-height: 27px;
  }
  .web-address::before, .web-address::after {
    content: ""; position: absolute; left: 0; right: 0; height: 1px;
    background: linear-gradient(90deg, transparent, #9a9a9a, transparent);
  }
  .web-address::before { top: 0; }
  .web-address::after { bottom: 0; }
</style>
</head>
<body>
<main class="canvas">

  <section class="card card-front" aria-label="Business card front">
    <svg class="card-art" viewBox="0 0 1008 624" preserveAspectRatio="none" aria-hidden="true">
      <defs>
        <linearGradient id="sheenTop" x1="0" y1="0" x2="1" y2="0">
          <stop offset="0" stop-color="#3a3a3a"/>
          <stop offset="0.5" stop-color="#777"/>
          <stop offset="1" stop-color="#111"/>
        </linearGradient>
        <linearGradient id="redFold" x1="0" y1="0" x2="1" y2="1">
          <stop offset="0" stop-color="#e8202a"/>
          <stop offset="0.6" stop-color="#c91c24"/>
          <stop offset="1" stop-color="#8e151b"/>
        </linearGradient>
        <linearGradient id="baseBand" x1="0" y1="0" x2="0" y2="1">
          <stop offset="0" stop-color="#5c5c5c"/>
          <stop offset="1" stop-color="#1e1e1e"/>
        </linearGradient>
        <linearGradient id="baseRed" x1="0" y1="0" x2="1" y2="0">
          <stop offset="0" stop-color="#e8202a"/>
          <stop offset="0.7" stop-color="#d01e26"/>
          <stop offset="1" stop-color="#a81c22"/>
        </linearGradient>
      </defs>
      <polygon points="335,0 755,0 275,62" fill="url(#sheenTop)"/>
      <polygon points="0,0 335,0 0,335" fill="var(--red)"/>
      <polygon points="67,0 270,0 0,215 0,68" fill="url(#redFold)"/>
      <line x1="0" y1="68" x2="67" y2="0" stroke="#d8d8d8" stroke-width="1.5"/>
      <line x1="0" y1="215" x2="270" y2="0" stroke="#d8d8d8" stroke-width="1.5"/>
      <line x1="0" y1="335" x2="335" y2="0" stroke="#d8d8d8" stroke-width="1.5"/>
      <rect x="0" y="576" width="1008" height="48" fill="url(#baseBand)"/>
      <polygon points="205,624 510,576 1008,576 1008,624" fill="url(#baseRed)"/>
      <polygon points="620,600 1008,576 1008,598" fill="#b51d24" opacity="0.8"/>
    </svg>

    <div class="wordmark">PIMLU</div>

    <div class="agent-photo" role="img" aria-label="Portrait photograph of the agent"></div>
    <h1 class="agent-name">OWEN CARTER</h1>
    <p class="agent-role">Licenced Real Estate Agent</p>

    <ul class="contact contact-direct">
      <li>0400 555 018</li>
      <li>1300 555 219</li>
      <li>owen@pimlu.com</li>
    </ul>
    <ul class="contact contact-office">
      <li>PO Box 7316</li>
      <li>Larkdale NSW 2790</li>
      <li>www.pimlu.com</li>
    </ul>
  </section>

  <section class="card card-back" aria-label="Business card back">
    <svg class="card-art" viewBox="0 0 1008 624" preserveAspectRatio="none" aria-hidden="true">
      <defs>
        <linearGradient id="sheenBase" x1="0" y1="0" x2="1" y2="0">
          <stop offset="0" stop-color="#111"/>
          <stop offset="0.5" stop-color="#777"/>
          <stop offset="1" stop-color="#3a3a3a"/>
        </linearGradient>
        <linearGradient id="redFoldBack" x1="0" y1="0" x2="1" y2="1">
          <stop offset="0" stop-color="#8e151b"/>
          <stop offset="0.4" stop-color="#c91c24"/>
          <stop offset="1" stop-color="#e8202a"/>
        </linearGradient>
      </defs>
      <polygon points="355,624 747,574 697,624" fill="url(#sheenBase)"/>
      <polygon points="1008,313 1008,624 697,624" fill="var(--red)"/>
      <polygon points="1008,430 1008,580 965,624 765,624" fill="url(#redFoldBack)"/>
      <line x1="697" y1="624" x2="1008" y2="313" stroke="#d8d8d8" stroke-width="1.5"/>
      <line x1="765" y1="624" x2="1008" y2="430" stroke="#d8d8d8" stroke-width="1.5"/>
      <line x1="965" y1="624" x2="1008" y2="580" stroke="#d8d8d8" stroke-width="1.5"/>
    </svg>

    <div class="wordmark">PIMLU</div>
    <p class="web-address">www.pimlu.com</p>
  </section>

</main>
</body>
</html>
```